New Business Card Design Project

We require a business card design for Vexalund, a newly established Indian company.
Our focus is on the development, manufacturing, and export of a diverse array of pharmaceutical products on a global scale. The card should convey a professional appearance, as our primary markets are in Africa, China, and Southeast Asian nations.
We envision a two-sided business card, with the reverse side dedicated to a logo set against a solid color or an elegantly designed pattern. The corners should be rounded. We would appreciate seeing both horizontal and vertical design options. We trust the designer to utilize their expertise in creating this design.

The content for the business card is included in the attached Word file.

Target Market(s)

Our primary markets are in Africa, China, and Southeast Asian, Latin America, Maldives, Sri Lanka

Industry/Entity Type

Pharmaceutical Manufacturing and Export

Contact Information for Business Card

Colors

Designer to choose colors to be used in the design.

Requirements
Must have
• The reverse side of the business card features solely the logo along with the tagline, "CARE BEYOND CURES."
Should not have
• The logo should not exceed two instances, encompassing both the front and back sides of the card.

```html
<!DOCTYPE html>
<html lang="en">
<head>
<meta charset="utf-8">
<title>Vexalund Business Card</title>
<link href="https://fonts.googleapis.com/css2?family=Poppins:wght@300;400;600&display=swap" rel="stylesheet">
<style>
  :root {
    --bg: #2a2a2a;
    --card: #ffffff;
    --brand-blue: #29a8e0;
    --brand-coral: #ef5f4c;
    --grad-coral: #c6706b;
    --grad-mid: #6fa2c3;
    --ink: #1d1d1d;
    --rule: #b9b9b9;
  }
  * { box-sizing: border-box; margin: 0; padding: 0; }
  html, body {
    width: 1093px; height: 1200px; overflow: hidden;
    background: var(--bg);
    font-family: 'Poppins', sans-serif;
  }
  .card {
    position: absolute;
    left: 262px;
    width: 578px; height: 356px;
    border-radius: 27px;
    overflow: hidden;
  }
  .card--front { top: 226px; background: var(--card); }
  .card--back {
    top: 621px;
    background: linear-gradient(to top right,
      var(--grad-coral) 0%, var(--grad-mid) 20%, var(--brand-blue) 42%,
      var(--brand-blue) 58%, var(--grad-mid) 80%, var(--grad-coral) 100%);
  }

  /* Front: brand block */
  .brand {
    position: absolute; left: 24px; top: 0; width: 240px; height: 356px;
    display: flex; align-items: center; justify-content: center; gap: 10px;
  }
  .brand__dot {
    width: 16px; height: 16px; border-radius: 50%;
    background: var(--brand-coral);
  }
  .brand__name {
    font-weight: 600; font-size: 44px; color: var(--brand-blue);
    letter-spacing: -0.5px;
  }
  .divider {
    position: absolute; left: 289px; top: 74px; width: 1px; height: 210px;
    background: var(--rule);
  }

  /* Front: details */
  .details {
    position: absolute; left: 314px; top: 76px;
    color: var(--ink); font-size: 17px; line-height: 21px;
  }
  .details__name {
    font-weight: 600; font-size: 24px; line-height: 26px;
    color: var(--brand-blue);
  }
  .details__role { margin-bottom: 14px; }
  .contact { list-style: none; margin-bottom: 14px; }
  .contact__item { display: flex; align-items: center; gap: 8px; }
  .contact__icon { width: 16px; height: 16px; flex: none; }
  .contact__icon * { fill: none; stroke: var(--brand-blue); stroke-width: 1.6; }
  .contact__icon .solid { fill: var(--brand-blue); stroke: none; }

  /* Back */
  .back__name {
    position: absolute; left: 0; right: 0; top: 128px; text-align: center;
    font-weight: 600; font-size: 64px; color: #fff; letter-spacing: -1px;
  }
  .back__tagline {
    position: absolute; left: 0; right: 0; top: 288px; text-align: center;
    font-weight: 400; font-size: 18px; color: #fff;
  }
</style>
</head>
<body>
  <section class="card card--front">
    <div class="brand">
      <span class="brand__dot"></span>
      <span class="brand__name">Vexalund</span>
    </div>
    <div class="divider"></div>
    <div class="details">
      <p class="details__name">Arjun K. Malvade</p>
      <p class="details__role">CEO<br>Vexalund</p>
      <ul class="contact">
        <li class="contact__item">
          <svg class="contact__icon" viewBox="0 0 16 16"><path d="M4 2 L6 5 L4.5 6.5 Q6 10 9.5 11.5 L11 10 L14 12 L12.5 14 Q6 13.5 2 4 Z"/></svg>
          +919800112233
        </li>
        <li class="contact__item">
          <svg class="contact__icon" viewBox="0 0 16 16"><rect class="solid" x="1" y="3.5" width="14" height="9"/><path d="M1 3.5 L8 9 L15 3.5" style="stroke:#fff"/></svg>
          amalvade@vexalund.com
        </li>
        <li class="contact__item">
          <svg class="contact__icon" viewBox="0 0 16 16"><circle cx="8" cy="8" r="6.5"/><ellipse cx="8" cy="8" rx="3" ry="6.5"/><path d="M1.5 8 H14.5 M2.5 5 H13.5 M2.5 11 H13.5"/></svg>
          https://vexalund.com/
        </li>
      </ul>
      <p class="details__address">12, Sarovar Colony,<br>Nandpur, 441208, India</p>
    </div>
  </section>

  <section class="card card--back">
    <p class="back__name">Vexalund</p>
    <p class="back__tagline">CARE BEYOND CURES.</p>
  </section>
</body>
</html>
```